RWT Fittings Ltd Business Cards

We need a business card with our business logo. We provide window and door installations on high-rises in west coast British Colombia, Canada.

I would like my business information and details on one side of the card, and the other side the company name with logo

Target Market(s)

General Contractors

Industry/Entity Type

Construction

Contact Information for Business Card

one side i want my company name and logo in the dark theme logo that i provided

Requirements
Must have
• Marco Peltieri, 16045518293, RWTFittings@mailbox-demo.com, 1407-5194 Linden Row Burnaby BC, V5H 2K9, Owner & Manager

```html
<!DOCTYPE html>
<html lang="en">
<head>
<meta charset="utf-8">
<title>RWT Fittings Ltd – Business Cards</title>
<link rel="stylesheet" href="https://fonts.googleapis.com/css2?family=Roboto:wght@400;500;700&display=swap">
<style>
  :root{
    --page-bg:#232323;
    --card-bg:#1e1f23;
    --card-back-bg:#1c1a18;
    --accent:#29a8e0;
    --name-grey:#a7a7a7;
    --text-light:#e6e6e6;
    --shadow:rgba(0,0,0,.55);
  }
  *{box-sizing:border-box;margin:0;padding:0}
  html,body{width:1200px;height:780px;overflow:hidden}
  body{
    background:var(--page-bg);
    font-family:"Roboto",Arial,sans-serif;
    display:flex;align-items:center;justify-content:center;gap:48px;
  }
  .card{
    position:relative;width:530px;height:303px;
    box-shadow:0 18px 40px var(--shadow);
    overflow:hidden;
  }
  /* Info side */
  .card--info{background:var(--card-bg)}
  .contact{
    position:absolute;left:34px;top:34px;
  }
  .contact__name{
    border-left:4px solid var(--accent);
    padding-left:10px;
    font-weight:700;font-size:27px;line-height:1;
    color:var(--name-grey);
  }
  .contact__name .first{color:var(--accent)}
  .contact__role{
    margin:6px 0 14px 14px;
    font-size:12.5px;color:var(--text-light);
  }
  .contact__address{
    font-size:12.5px;line-height:1.45;color:var(--text-light);
    margin-bottom:10px;
  }
  .contact__row{
    display:flex;align-items:center;gap:8px;
    font-size:12.5px;line-height:1.7;color:var(--text-light);
  }
  .contact__row svg{width:13px;height:13px;flex:none}
  .brand{
    position:absolute;right:34px;bottom:34px;
    display:flex;align-items:center;gap:12px;
  }
  .brand__mark{width:22px;height:22px;background:var(--accent)}
  .brand__name{
    font-weight:700;font-size:30px;color:var(--accent);letter-spacing:.5px;
  }
  /* Logo side */
  .card--logo{background:var(--card-back-bg)}
  .card__photo{
    position:absolute;inset:0;
    background:linear-gradient(135deg,#161514 0%,#2a2724 45%,#3b3733 75%,#2a2825 100%);
  }
  .card--logo .brand{
    right:auto;bottom:auto;left:50%;top:50%;
    transform:translate(-50%,-50%);
  }
</style>
</head>
<body>
  <section class="card card--info" aria-label="Business card, contact side">
    <div class="contact">
      <h1 class="contact__name"><span class="first">Marco</span> Peltieri</h1>
      <p class="contact__role">Owner &amp; Manager</p>
      <p class="contact__address">1407-5194 Linden Row<br>Burnaby BC, V5H 2K9</p>
      <p class="contact__row">
        <svg viewBox="0 0 24 24" aria-hidden="true"><path fill="var(--accent)" d="M6.6 10.8a15.1 15.1 0 0 0 6.6 6.6l2.2-2.2c.3-.3.7-.4 1-.2 1.1.4 2.3.6 3.6.6.6 0 1 .4 1 1V20c0 .6-.4 1-1 1A17 17 0 0 1 3 4c0-.6.4-1 1-1h3.5c.6 0 1 .4 1 1 0 1.3.2 2.5.6 3.6.1.3 0 .7-.2 1z"/></svg>
        1604 551 8293
      </p>
      <p class="contact__row">
        <svg viewBox="0 0 24 24" aria-hidden="true"><rect x="2" y="5" width="20" height="14" rx="2" fill="var(--accent)"/><path d="M3 6l9 7 9-7" stroke="var(--card-bg)" stroke-width="1.8" fill="none"/></svg>
        RWTFittings@mailbox-demo.com
      </p>
    </div>
    <div class="brand">
      <span class="brand__mark" aria-hidden="true"></span>
      <span class="brand__name">RWT Fittings Ltd</span>
    </div>
  </section>

  <section class="card card--logo" aria-label="Business card, company side">
    <div class="card__photo" role="img" aria-label="Dim photograph of a modern interior with a potted plant"></div>
    <div class="brand">
      <span class="brand__mark" aria-hidden="true"></span>
      <span class="brand__name">RWT Fittings Ltd</span>
    </div>
  </section>
</body>
</html>
```